Commercial/Corporate Law Firm needs Website Design

Hi guys. I've started up a new law firm and would love your help designing an attractive website. I'll need both design and coding, and to make it easy for us to edit as necessary later, I think it should be built off a Wordpress.org structure.
FIRST IMPRESSIONS
It's very important that the first impression of the website really captures our prospective clients' attention and impresses them. Their first three seconds needs to be good.
I imagine the homepage may be short, with a menu bar and a compelling image, and with a tagline overlaid or underneath (eg. "It's about results.")
The image should be related to our practice areas: eg. IPOs, corporate transactions, or commercial negotiations.
I have previously suggested there could be a skyline image of Sydney or Adelaide. However, because we are based in Adelaide, I don't think Sydney is appropriate - and Adelaide is probably too boring to use.
HOMEPAGE
Being a new firm, we don't have many existing testimonials, and I will be the only lawyer to start with. So we need to focus on the nature of the services we will provide and how my experience can help them. We have an existing logo to use, and I would like the website colour scheme not to clash with that logo (dark blue and white).
After the initial image and tagline there should be a brief introduction to each of the main areas of work, eg. "We specialise in three main areas of practice:"
1. Corporate Transactions and Regulation
2. Business Law and Dispute Resolution
3. Migration Assistance
These should each have an appropriate photo and link to a separate page that briefly describes our services in that area.
Below that there should be a message from me with a photo. Finally, at the bottom, there should be a "Contact Us" section which shows a Google image of our address, contact details, and then our logo with colours inverted.
OTHER PAGES
While we will need some other pages, they should all be fairly simple. I think we will need one page to say "About Us", where I will put information about my experience. I think we will then need one page for each of the 3 areas listed above, which just needs an appropriate image and then text to describe the service. Finally, a "Contact Us" page which I imagine will be the same as the bottom of the homepage.
OTHER DETAILS
For now you can use details from my LinkedIn page to fill out any other text as necessary, or the photo.
Because the logo is square, I would prefer the design of the website also to be rectangular.
Looking forward to seeing your work! Thank you.
Marcus
Potential clients:
Businesses with legal issues or disputes
Companies wishing to list on the stock market

```html
<!DOCTYPE html>
<html lang="en">
<head>
<meta charset="utf-8">
<title>Verrano Legal</title>
<link href="https://fonts.googleapis.com/css2?family=Cinzel:wght@400&family=Lato:ital,wght@0,400;0,700;1,400&family=Roboto:wght@400&display=swap" rel="stylesheet">
<style>
  :root{
    --navy:#0b2a5c;
    --royal:#0d3f8f;
    --footer:#06398a;
    --ink:#222a35;
    --grey:#7a7f86;
    --line:#d4d7dc;
    --white:#ffffff;
    --sky-top:#e9f1fa;
    --sky-mid:#b9d3ec;
    --park:#5f8f3c;
    --band-top:#c9cacc;
    --band-bottom:#ececed;
  }
  *{margin:0;padding:0;box-sizing:border-box}
  html,body{width:1200px;height:2691px;overflow:hidden;background:var(--white)}
  body{position:relative;font-family:"Lato",Arial,sans-serif;color:var(--ink)}
  h1,h2,h3{font-weight:400}
  .abs{position:absolute}

  /* hero */
  .hero{left:0;top:0;width:1200px;height:745px;overflow:hidden}
  .hero-photo{position:absolute;inset:0;
    background:linear-gradient(180deg,var(--sky-top) 0%,#dbe8f5 22%,var(--sky-mid) 42%,#c9b08a 55%,#7d9a5a 66%,var(--park) 76%,#9fc2d8 86%,#e8eef3 100%)}
  .hero-wave{position:absolute;left:0;bottom:0;width:1200px;height:140px}
  .nav{position:absolute;top:56px;display:flex;gap:33px;font-weight:700;font-size:15px;color:var(--navy);letter-spacing:.2px;white-space:nowrap}
  .nav a{color:inherit;text-decoration:none;padding-bottom:9px}
  .nav a.current{border-bottom:2px solid var(--navy)}
  .nav-left{left:181px}
  .nav-right{left:753px}
  .brand{position:absolute;left:0;width:1200px;top:22px;display:flex;flex-direction:column;align-items:center}
  .brand-mark{width:62px;height:62px;background:var(--navy)}
  .brand-name{margin-top:14px;font-family:"Lato",Arial,sans-serif;font-weight:400;font-size:21px;letter-spacing:4px;color:var(--navy);white-space:nowrap}
  .hero-title{left:0;width:1200px;top:252px;text-align:center;font-family:"Cinzel",Georgia,serif;font-weight:400;font-size:56px;letter-spacing:2px;color:var(--navy)}
  .hero-sub{left:0;width:1200px;top:330px;text-align:center;font-style:italic;font-size:22px;line-height:29px;color:var(--navy)}
  .hero-arrow{width:52px;height:52px;top:297px}

  /* practice */
  .practice-kicker{left:0;width:1200px;top:786px;text-align:center;font-size:23px;color:var(--royal)}
  .practice-head{left:0;width:1200px;top:818px;text-align:center;font-size:32px;color:var(--royal)}
  .area{width:320px;top:883px;display:flex;flex-direction:column;align-items:center;text-align:center}
  .area-photo{width:226px;height:226px;border-radius:50%}
  .area-title{margin-top:28px;font-family:"Roboto",Arial,sans-serif;font-weight:400;font-size:20px;line-height:26px;color:var(--ink)}
  .area-text{margin-top:14px;width:280px;font-size:12.5px;line-height:18px;color:var(--grey)}
  .read-more{margin-top:18px;width:125px;height:36px;border:2px solid var(--navy);font-weight:700;font-size:12px;color:var(--navy);display:flex;align-items:center;justify-content:center}

  /* message */
  .message{left:0;top:1372px;width:1200px;height:566px;overflow:hidden;
    background:linear-gradient(180deg,var(--band-top) 0%,#dcdcdd 45%,#bdbec0 72%,var(--band-bottom) 100%)}
  .message-wave{position:absolute;left:0;bottom:0;width:1200px;height:110px}
  .portrait{position:absolute;left:150px;top:28px;width:410px;height:538px;
    background:linear-gradient(180deg,#b9a190 0%,#8f7a6c 30%,#2a2f3c 46%,#1d2230 100%);
    border-radius:170px 170px 0 0}
  .message-title{position:absolute;z-index:2;left:585px;top:175px;font-size:40px;color:var(--ink)}
  .message-text{position:absolute;z-index:2;left:585px;top:240px;width:500px;font-style:italic;font-size:21px;line-height:36px;color:#4a4f57}

  /* contact */
  .contact-head{left:0;width:1200px;top:2056px;text-align:center;font-size:32px;color:var(--royal)}
  .map{left:143px;top:2146px;width:494px;height:306px;background:linear-gradient(135deg,#e4e4e4,#cfcfcf)}
  .info{left:700px;display:flex;gap:20px}
  .info-icon{width:40px;height:40px;border:1px solid var(--line);display:flex;align-items:center;justify-content:center}
  .info-label{font-size:17px;color:var(--royal);line-height:20px}
  .info-value{font-size:16px;color:#4a4f57;line-height:22px;margin-top:2px;white-space:nowrap}
  .social{left:704px;top:2377px;display:flex;gap:8px}
  .social span{width:43px;height:43px;border:2px solid var(--navy);border-radius:50%;display:block}

  /* footer */
  .footer{left:0;top:2533px;width:1200px;height:158px;background:var(--footer)}
  .footer-nav{position:absolute;left:118px;top:48px;display:flex;gap:33px;font-weight:700;font-size:15px;color:var(--white);white-space:nowrap}
  .footer-copy{position:absolute;left:118px;top:85px;font-size:12px;color:#dfe6f3}
  .footer-brand{position:absolute;left:870px;width:250px;top:22px;display:flex;flex-direction:column;align-items:center}
  .footer-brand .brand-mark{width:52px;height:52px;background:var(--white)}
  .footer-brand .brand-name{color:var(--white);font-size:19px;margin-top:12px}
</style>
</head>
<body>

<header class="hero abs">
  <div class="hero-photo" role="img" aria-label="City skyline beside a riverside park and fountain under a bright sky"></div>
  <svg class="hero-wave" viewBox="0 0 1200 140" preserveAspectRatio="none" aria-hidden="true">
    <path d="M0 70 C260 20 480 40 700 90 C900 135 1060 110 1200 80 L1200 140 L0 140 Z" fill="#ffffff" opacity=".55"/>
    <path d="M0 105 C300 60 520 80 760 115 C950 140 1100 125 1200 110 L1200 140 L0 140 Z" fill="#ffffff"/>
  </svg>

  <nav class="nav nav-left">
    <a class="current">HOME</a><a>ABOUT US</a><a>OUR SERVICERS</a>
  </nav>
  <div class="brand">
    <div class="brand-mark"></div>
    <div class="brand-name">VERRANO LEGAL</div>
  </div>
  <nav class="nav nav-right">
    <a>WHY US</a><a>BLOGS</a><a>CONTACT US</a>
  </nav>

  <h1 class="hero-title abs">IT'S ABOUT RESULTS</h1>
  <p class="hero-sub abs">Class aptent taciti sociosqu ad litora torquent per conubia nostra per<br>inceptos hymenaeos Proin nulla arcu nonummy</p>

  <svg class="hero-arrow abs" style="left:67px" viewBox="0 0 52 52" aria-label="Previous slide">
    <circle cx="26" cy="26" r="24" fill="none" stroke="#1b1f27" stroke-width="2"/>
    <path d="M29 17 L20 26 L29 35" fill="none" stroke="#1b1f27" stroke-width="3"/>
  </svg>
  <svg class="hero-arrow abs" style="left:1072px" viewBox="0 0 52 52" aria-label="Next slide">
    <circle cx="26" cy="26" r="24" fill="none" stroke="#1b1f27" stroke-width="2"/>
    <path d="M23 17 L32 26 L23 35" fill="none" stroke="#1b1f27" stroke-width="3"/>
  </svg>
</header>

<section>
  <p class="practice-kicker abs">WE SPECIALISE IN THREE</p>
  <h2 class="practice-head abs">MAIN AREAS OF PRACTICE</h2>

  <article class="area abs" style="left:122px">
    <div class="area-photo" role="img" aria-label="Business team silhouetted in a bright glass meeting room" style="background:linear-gradient(160deg,#dfe8f4,#7d95b8 55%,#1c2740)"></div>
    <h3 class="area-title">Corporate Transactions<br>and Regulation</h3>
    <p class="area-text">Class aptent taciti sociosqu ad litora torquent per conubia nostra per inceptos hymenaeos Proin nulla arcu nonummy luctus</p>
    <div class="read-more">READ MORE</div>
  </article>

  <article class="area abs" style="left:446px">
    <div class="area-photo" role="img" aria-label="Hand signing a document with a pen" style="background:linear-gradient(150deg,#2a1c16,#6b4a38 50%,#e4e1dc)"></div>
    <h3 class="area-title">Business Law and<br>Dispute Resolution</h3>
    <p class="area-text">Class aptent taciti sociosqu ad litora torquent per conubia nostra per inceptos hymenaeos Proin nulla arcu nonummy luctus</p>
    <div class="read-more">READ MORE</div>
  </article>

  <article class="area abs" style="left:773px">
    <div class="area-photo" role="img" aria-label="Flock of birds flying across a sunset sky" style="background:linear-gradient(180deg,#7f8fa8,#c9a87a 55%,#f2c24a)"></div>
    <h3 class="area-title">Migration<br>Assistance</h3>
    <p class="area-text">Class aptent taciti sociosqu ad litora torquent per conubia nostra per inceptos hymenaeos Proin nulla arcu nonummy</p>
    <div class="read-more">READ MORE</div>
  </article>
</section>

<section class="message abs">
  <div class="portrait" role="img" aria-label="Portrait of the principal lawyer in a dark suit and red tie"></div>
  <svg class="message-wave" viewBox="0 0 1200 110" preserveAspectRatio="none" aria-hidden="true">
    <path d="M0 60 C250 20 480 40 700 70 C900 95 1080 70 1200 50 L1200 110 L0 110 Z" fill="#ffffff" opacity=".6"/>
    <path d="M0 95 C300 60 560 70 800 92 C980 108 1120 100 1200 92 L1200 110 L0 110 Z" fill="#ffffff"/>
  </svg>
  <h2 class="message-title">My Message</h2>
  <p class="message-text">Praesent elementum elit at tellus nec ultricies sit amet porttitor mattis enim In massa libero interdum nec interdum vel blandit sed nulla In ullamcorper est eget tempor cursus neque mi</p>
</section>

<section>
  <h2 class="contact-head abs">CONTACT US</h2>
  <div class="map abs" role="img" aria-label="Street map showing the office location"></div>

  <div class="info abs" style="top:2141px">
    <div class="info-icon">
      <svg width="18" height="22" viewBox="0 0 18 22" aria-hidden="true"><path d="M9 1 C4.5 1 1.5 4.3 1.5 8.3 C1.5 13.5 9 21 9 21 C9 21 16.5 13.5 16.5 8.3 C16.5 4.3 13.5 1 9 1 Z" fill="none" stroke="#0b2a5c" stroke-width="2"/><circle cx="9" cy="8.3" r="2.6" fill="#0b2a5c"/></svg>
    </div>
    <div><div class="info-label">OUR ADDRESS</div><div class="info-value">48 Torrens Lane, Suite 5, Kestrel Bay 5071</div></div>
  </div>

  <div class="info abs" style="top:2218px">
    <div class="info-icon">
      <svg width="22" height="22" viewBox="0 0 22 22" aria-hidden="true"><path d="M5 2 L8.5 2 L10 7 L7.5 8.8 C8.7 11.4 10.6 13.3 13.2 14.5 L15 12 L20 13.5 L20 17 C20 18.7 18.7 20 17 20 C9 19.5 2.5 13 2 5 C2 3.3 3.3 2 5 2 Z" fill="none" stroke="#0b2a5c" stroke-width="1.8"/></svg>
    </div>
    <div><div class="info-label">PHONE NUMBER</div><div class="info-value">(08) 7010 4826</div></div>
  </div>

  <div class="info abs" style="top:2290px">
    <div class="info-icon">
      <svg width="22" height="16" viewBox="0 0 22 16" aria-hidden="true"><rect x="1" y="1" width="20" height="14" fill="none" stroke="#0b2a5c" stroke-width="1.8"/><path d="M1 1 L11 9 L21 1" fill="none" stroke="#0b2a5c" stroke-width="1.8"/></svg>
    </div>
    <div><div class="info-label">EMAIL US</div><div class="info-value">hello@verranolegal.example</div></div>
  </div>

  <div class="social abs" aria-label="Social media links">
    <span aria-label="Social link one"></span>
    <span aria-label="Social link two"></span>
    <span aria-label="Social link three"></span>
    <span aria-label="Social link four"></span>
  </div>
</section>

<footer class="footer abs">
  <nav class="footer-nav">
    <a>HOME</a><a>ABOUT US</a><a>OUR SERVICERS</a><a>WHY US</a><a>BLOGS</a><a>CONTACT US</a>
  </nav>
  <p class="footer-copy">© 2018 Company Name &nbsp;All right reserved</p>
  <div class="footer-brand">
    <div class="brand-mark"></div>
    <div class="brand-name">VERRANO LEGAL</div>
  </div>
</footer>

</body>
</html>
```